Private Investigation Business Card Design

I need a business card for a new private investigation company named Brisk Inquiries. I perform mainly surveillance jobs, vehicle repossessions, document serves etc. The final design should aim for a professional look. The logo has a magnifying glass with stick man arms and legs and is in a running action to show the "Brisk" aspect of the name. If the colour scheme could remain the same as the website www.briskinquiries-demo.com.au with silvers,blacks and a couple electric blue highlights.
Industry/Entity Type
Business
Contact Information for Business Card
Morgan Kellaway
Brisk Inquiries
0487316204
PO Box 58, Carnwell NSW 2291
info@briskinquiries-demo.com.au
www.briskinquiries-demo.com.au
Look and feel

```html
<!DOCTYPE html>
<html lang="en">
<head>
<meta charset="utf-8">
<title>Brisk Inquiries – Business Card</title>
<link rel="stylesheet" href="https://fonts.googleapis.com/css2?family=Arimo:wght@400;700&family=Questrial&display=swap">
<style>
  :root {
    --page-bg: #ece8e1;
    --card-dark: #231f20;
    --card-light: #ffffff;
    --silver: #a9a9ad;
    --silver-deep: #8a8a8e;
    --band-top: #e2e2e4;
    --band-mid: #b4b4b8;
    --band-bottom: #d6d6d8;
    --ink: #231f20;
    --ink-soft: #3a3a3c;
    --icon-bg: #8c8c90;
  }
  * { margin: 0; padding: 0; box-sizing: border-box; }
  html, body {
    width: 1189px; height: 1200px; overflow: hidden;
    background: var(--page-bg);
  }
  .canvas { position: relative; width: 1189px; height: 1200px; }
  .card {
    position: absolute; left: 198px; width: 793px; height: 487px;
    border-radius: 18px; overflow: hidden;
    box-shadow: 4px 6px 10px rgba(0,0,0,0.35);
  }
  .card--front { top: 68px; background: var(--card-dark); }
  .card--back { top: 626px; background: var(--card-light); }

  .wordmark { position: absolute; font-family: "Questrial", sans-serif; color: var(--silver); }
  .wordmark__name { display: block; line-height: 1; }
  .wordmark__sub { display: block; line-height: 1; }

  .card--front .wordmark { left: 0; width: 100%; top: 168px; text-align: center; }
  .card--front .wordmark__name { font-size: 118px; letter-spacing: 4px; }
  .card--front .wordmark__sub { font-size: 37px; letter-spacing: 13px; margin-top: 6px; padding-left: 13px; }

  .web-band {
    position: absolute; left: 0; top: 379px; width: 100%; height: 40px;
    background: linear-gradient(to bottom, var(--band-top), var(--band-mid) 55%, var(--band-bottom));
    display: flex; align-items: center; justify-content: center;
    font-family: "Questrial", sans-serif; font-size: 21px; letter-spacing: 0.6px; color: var(--ink-soft);
  }

  .card--back .wordmark { left: 52px; top: 66px; color: var(--silver-deep); display: flex; align-items: center; gap: 28px; }
  .card--back .wordmark__name { font-size: 104px; letter-spacing: 3px; }
  .card--back .wordmark__sub { font-size: 33px; letter-spacing: 11px; margin-top: 4px; }
  .wordmark__dot { width: 46px; height: 46px; border-radius: 50%; background: var(--silver); flex: none; }

  .name-rule { position: absolute; left: 52px; top: 275px; width: 371px; height: 2px; background: var(--ink); }
  .person-name {
    position: absolute; right: 51px; top: 259px;
    font-family: "Arimo", sans-serif; font-size: 31px; letter-spacing: 0.5px; color: var(--ink);
  }

  .contact-list { position: absolute; left: 52px; top: 350px; list-style: none; }
  .contact-list li {
    display: flex; align-items: center; height: 29px;
    font-family: "Questrial", sans-serif; font-size: 21px; letter-spacing: 0.6px; color: var(--ink);
  }
  .contact-icon {
    width: 23px; height: 23px; background: var(--icon-bg); margin-right: 15px; flex: none;
  }
  .postal-address {
    position: absolute; right: 51px; top: 385px; text-align: right;
    font-family: "Questrial", sans-serif; font-size: 21px; letter-spacing: 0.8px; line-height: 25px; color: var(--ink);
  }
</style>
</head>
<body>
<main class="canvas">
  <section class="card card--front" aria-label="Card front">
    <div class="wordmark">
      <span class="wordmark__name">Brisk</span>
      <span class="wordmark__sub">INQUIRIES</span>
    </div>
    <div class="web-band">www.briskinquiries-demo.com.au</div>
  </section>

  <section class="card card--back" aria-label="Card back">
    <div class="wordmark">
      <div>
        <span class="wordmark__name">Brisk</span>
        <span class="wordmark__sub">INQUIRIES</span>
      </div>
      <span class="wordmark__dot"></span>
    </div>

    <div class="name-rule"></div>
    <div class="person-name">MORGAN KELLAWAY</div>

    <ul class="contact-list">
      <li>
        <svg class="contact-icon" viewBox="0 0 23 23" aria-hidden="true">
          <rect width="23" height="23" fill="#8c8c90"/>
          <path d="M7 4 L10 4 L10.5 8 L8.8 9.2 Q10 13 13.8 14.2 L15 12.5 L19 13 L19 16 Q18 19 14 18 Q6 15 4.5 8 Q4.5 5 7 4 Z" fill="#fff"/>
        </svg>
        0487316204
      </li>
      <li>
        <svg class="contact-icon" viewBox="0 0 23 23" aria-hidden="true">
          <rect width="23" height="23" fill="#8c8c90"/>
          <rect x="4" y="6.5" width="15" height="10" fill="#fff"/>
          <path d="M4 6.5 L11.5 12.5 L19 6.5 M4 16.5 L9.5 11 M19 16.5 L13.5 11" stroke="#8c8c90" stroke-width="1.2" fill="none"/>
        </svg>
        info@briskinquiries-demo.com.au
      </li>
      <li>
        <svg class="contact-icon" viewBox="0 0 23 23" aria-hidden="true">
          <rect width="23" height="23" fill="#8c8c90"/>
          <g stroke="#fff" stroke-width="1.2" fill="none">
            <circle cx="11.5" cy="11.5" r="7"/>
            <ellipse cx="11.5" cy="11.5" rx="3" ry="7"/>
            <path d="M4.5 11.5 H18.5 M5.5 8 H17.5 M5.5 15 H17.5"/>
          </g>
        </svg>
        www.briskinquiries-demo.com.au
      </li>
    </ul>

    <address class="postal-address" style="font-style: normal;">
      PO Box 58, Carnwell<br>NSW 2291
    </address>
  </section>
</main>
</body>
</html>
```